NZ First of it's kind solutions directory and marketplace for busy Mums needs a business card design

We need a business card design for our new nationwide business in NZ (long term plans to go global). We provide solutions to the everyday challenges that busy Mums face by connecting them with quality communities and suppliers of carefully selected, relevant products and services. We sell direct via our online marketplace. The final design should communicate our values of inclusivity, quality and smart solutions. Colours should incorporate our logo colour palette of #477077 and #6ba8b2. Our website is at https://www.brightnestmums.example

Target Market(s)

busy Mums, Age 28 – 50, female, income over $100K, location main centres NZ primarily but NZ wide. Is likely juggling work or career with a young family. Probably had hobbies which have fallen by the wayside.
-Wants to succeed in her chosen career without compromising on family life
-to successfully juggle her career without feeling like she is compromising her children
- Is time poor, something always has to give and it’s generally her health (she’ll stay up late, get stressed)
- probably ex corporate or professional career. Has discretional income

Industry/Entity Type

Business

Contact Information for Business Card

Lena Forbisher, Founder, BrightNestMums.example (Strapline Tap; Gather; Sorted), 47 Kowhai Terrace, Ellerslie, Auckland 1051, New Zealand. Mob: 021 483 517 Ph: +64 (0)9 571 4860

Font styles to use
Other font styles liked:
• Raleway, and/or Architects Daughter

Colors
00a990
33b8a4
86cfc6
cfeae6

Requirements
Must have
• the above details, streamline. the logo and colours associated with those logos
Should not have
• foil or metallic colours

```html
<!DOCTYPE html>
<html lang="en">
<head>
<meta charset="utf-8">
<title>BrightNestMums — Business Card</title>
<link href="https://fonts.googleapis.com/css2?family=Roboto:ital,wght@0,400;0,500;0,700;1,400&family=Roboto+Condensed:wght@400&display=swap" rel="stylesheet">
<style>
  :root {
    --page-bg: #ececec;
    --card-white: #f7f7f6;
    --teal-dark: #3d5c66;
    --teal-brand: #477077;
    --teal-light: #6ba8b2;
    --teal-mid: #5694a0;
    --ink-grey: #55595c;
    --on-dark: #ffffff;
  }
  * { box-sizing: border-box; margin: 0; padding: 0; }
  html, body { width: 1200px; height: 576px; overflow: hidden; }
  body {
    background: var(--page-bg);
    position: relative;
    font-family: "Roboto", Arial, sans-serif;
  }
  .card {
    position: absolute;
    top: 138px;
    width: 484px;
    height: 294px;
    border-radius: 12px;
    background: var(--card-white);
    overflow: hidden;
  }
  .card--front { left: 82px; }
  .card--back { left: 602px; }

  /* Front */
  .front-brand {
    position: absolute;
    left: 32px;
    top: 130px;
    width: 244px;
    display: flex;
    align-items: center;
    gap: 9px;
    z-index: 1;
  }
  .brand-dot {
    width: 22px; height: 22px;
    flex: none;
    border-radius: 50%;
    background: var(--teal-brand);
  }
  .brand-name {
    font-weight: 500;
    font-size: 23.5px;
    color: var(--teal-brand);
    letter-spacing: -0.3px;
    line-height: 1;
    white-space: nowrap;
  }
  .front-strap {
    position: absolute;
    left: 63px;
    top: 163px;
    font-size: 9.5px;
    letter-spacing: 2.8px;
    color: var(--ink-grey);
    white-space: nowrap;
  }
  .strap-sep { color: var(--teal-light); margin: 0 3px; }
  .front-illustration {
    position: absolute;
    left: 288px;
    top: 22px;
    width: 196px;
    height: 272px;
    background: linear-gradient(180deg, var(--teal-light) 0%, var(--teal-mid) 30%, var(--teal-dark) 100%);
    border-top-left-radius: 98px;
  }

  /* Back */
  .back-panel { position: absolute; inset: 0; }
  .contact-name {
    position: absolute;
    left: 24px; top: 20px;
    font-weight: 700;
    font-size: 20px;
    color: var(--on-dark);
  }
  .contact-role {
    position: absolute;
    left: 24px; top: 46px;
    font-style: italic;
    font-size: 11.5px;
    color: var(--on-dark);
  }
  .contact-address {
    position: absolute;
    left: 24px; top: 152px;
    font-family: "Roboto Condensed", Arial, sans-serif;
    font-size: 12.5px;
    line-height: 18.5px;
    color: var(--on-dark);
  }
  .contact-list {
    position: absolute;
    left: 28px; top: 200px;
    list-style: none;
    font-family: "Roboto Condensed", Arial, sans-serif;
    font-size: 12.5px;
    line-height: 18.3px;
    color: var(--on-dark);
  }
  .contact-list li { display: flex; align-items: center; gap: 7px; }
  .contact-list svg { width: 11px; height: 11px; flex: none; }
  .back-brand-dot {
    position: absolute;
    left: 320px; top: 130px;
    width: 28px; height: 28px;
    border-radius: 50%;
    background: var(--teal-brand);
  }
  .back-brand {
    position: absolute;
    left: 412px; top: 146px;
    transform: translate(-50%, -50%) rotate(-90deg);
    white-space: nowrap;
    font-weight: 500;
    font-size: 28px;
    color: var(--teal-brand);
    letter-spacing: -0.3px;
  }
  .back-strap {
    position: absolute;
    left: 440px; top: 146px;
    transform: translate(-50%, -50%) rotate(-90deg);
    white-space: nowrap;
    font-size: 9px;
    letter-spacing: 2.8px;
    color: var(--ink-grey);
  }
</style>
</head>
<body>

<section class="card card--front" aria-label="Business card front">
  <div class="front-illustration" role="img" aria-label="Large teal shopping bag illustration"></div>
  <div class="front-brand">
    <span class="brand-dot"></span>
    <span class="brand-name">BrightNestMums</span>
  </div>
  <p class="front-strap">TAP<span class="strap-sep">|</span>GATHER<span class="strap-sep">|</span>SORTED</p>
</section>

<section class="card card--back" aria-label="Business card back">
  <svg class="back-panel" viewBox="0 0 484 294" preserveAspectRatio="none" aria-hidden="true">
    <path d="M0 0 H286 Q230 147 286 294 H0 Z" fill="var(--teal-dark)"/>
    <path d="M286 0 Q230 147 286 294" fill="none" stroke="var(--teal-light)" stroke-width="4"/>
  </svg>

  <h1 class="contact-name">Lena Forbisher</h1>
  <p class="contact-role">Founder</p>
  <p class="contact-address">47 Kowhai Terrace, Ellerslie,<br>Auckland 1051, New Zealand</p>
  <ul class="contact-list">
    <li>
      <svg viewBox="0 0 12 12" aria-hidden="true"><rect x="3" y="0.5" width="6" height="11" rx="1.2" fill="none" stroke="#fff" stroke-width="1.2"/><circle cx="6" cy="9.5" r="0.7" fill="#fff"/></svg>
      021 483 517
    </li>
    <li>
      <svg viewBox="0 0 12 12" aria-hidden="true"><path d="M1 4 Q6 0 11 4 L9.5 5.5 L8 4.5 L4 4.5 L2.5 5.5 Z" fill="#fff"/><rect x="2.5" y="6" width="7" height="5" rx="1" fill="#fff"/></svg>
      +64 (0)9 571 4860
    </li>
    <li>
      <svg viewBox="0 0 12 12" aria-hidden="true"><rect x="0.8" y="2.5" width="10.4" height="7" fill="none" stroke="#fff" stroke-width="1.1"/><path d="M0.8 2.5 L6 6.5 L11.2 2.5" fill="none" stroke="#fff" stroke-width="1.1"/></svg>
      www.BrightNestMums.example
    </li>
    <li>
      <svg viewBox="0 0 12 12" aria-hidden="true"><circle cx="6" cy="6" r="5" fill="none" stroke="#fff" stroke-width="1.1"/><ellipse cx="6" cy="6" rx="2.2" ry="5" fill="none" stroke="#fff" stroke-width="1"/><path d="M1 6 H11" stroke="#fff" stroke-width="1"/></svg>
      lenaforbisher@brightnestmums.example
    </li>
  </ul>

  <span class="back-brand-dot"></span>
  <span class="back-brand">BrightNestMums</span>
  <span class="back-strap">TAP<span class="strap-sep">|</span>GATHER<span class="strap-sep">|</span>SORTED</span>
</section>

</body>
</html>
```